New Business Card Design Project

Need a design that will create an impact / strong impression towards our clients for our business. We are in the lighting business and we do lighting retrofits for large commercial to industrial clientele.

Target Market(s)

Lighting Industry

Industry/Entity Type

Business

Font styles to use
Other font styles liked:
• we would like to use the font on our logo, not sure what it is though..

Requirements
Must have
• Our logo.
Nice to have
• We are open to suggestions that have to do with lighting.

```html
<!DOCTYPE html>
<html lang="en">
<head>
<meta charset="utf-8">
<title>Quillmoor Retrofit Group — Business Card</title>
<link href="https://fonts.googleapis.com/css2?family=Roboto:wght@400;500;700&family=Roboto+Condensed:wght@500;700&display=swap" rel="stylesheet">
<style>
  :root {
    --bg: #2b2b2b;
    --green-dark: #143d12;
    --green-mid: #1b7a34;
    --green-band: #1e6b2a;
    --paper: #f1f1f1;
    --ink: #4f4f4f;
    --rule: #9a9a9a;
    --white: #ffffff;
  }
  * { margin: 0; padding: 0; box-sizing: border-box; }
  html, body {
    width: 1200px; height: 960px; overflow: hidden;
    background: var(--bg);
    font-family: "Roboto", Arial, sans-serif;
  }
  .card {
    position: absolute; left: 320px; width: 600px; height: 342px;
    border-radius: 18px; overflow: hidden;
  }
  .card--front { top: 108px; background: var(--green-dark); }
  .card--back { top: 493px; background: var(--paper); }

  .front__brand {
    position: absolute; top: 132px; left: 0; width: 100%;
    text-align: center; color: var(--white);
    font-weight: 700; font-size: 46px; letter-spacing: 4px; line-height: 56px;
  }
  .front__url {
    position: absolute; top: 281px; left: 0; width: 100%;
    text-align: center; color: var(--white);
    font-size: 14px; letter-spacing: 2.6px;
  }

  .back__brand {
    position: absolute; top: 36px; right: 28px;
    display: flex; align-items: center; gap: 10px;
  }
  .back__brand-name {
    font-weight: 700; font-size: 34px; letter-spacing: 2px; color: var(--green-mid); line-height: 44px;
  }
  .back__brand-mark { width: 22px; height: 22px; background: var(--green-dark); }
  .back__brand-sub {
    position: absolute; top: 96px; right: 28px;
    font-weight: 500; font-size: 11px; letter-spacing: 1.2px; color: var(--green-mid);
  }

  .person { position: absolute; left: 27px; top: 164px; }
  .person__name {
    font-family: "Roboto Condensed", Arial, sans-serif; font-weight: 700;
    font-size: 23px; color: var(--green-dark); line-height: 1;
  }
  .person__title {
    font-family: "Roboto Condensed", Arial, sans-serif; font-weight: 500;
    font-size: 15px; color: var(--green-mid); margin-top: 5px; line-height: 1;
  }
  .divider {
    position: absolute; left: 27px; right: 27px; top: 213px;
    height: 1px; background: var(--rule);
  }
  .contacts { position: absolute; left: 27px; top: 226px; list-style: none; }
  .contacts li {
    display: flex; align-items: center; gap: 8px;
    font-size: 14px; color: var(--ink); height: 19px;
  }
  .contacts svg { width: 15px; height: 14px; fill: var(--green-dark); flex: none; }
  .address {
    position: absolute; right: 28px; top: 248px; text-align: right;
    font-size: 14px; color: var(--ink); line-height: 19px;
  }
  .band {
    position: absolute; left: 0; right: 0; bottom: 0; height: 16px;
    background: var(--green-band); border-top: 3px solid var(--paper);
    box-shadow: 0 -2px 0 var(--green-mid);
  }
</style>
</head>
<body>
  <section class="card card--front">
    <div class="front__brand">QUILLMOOR</div>
    <div class="front__url">www.quillmoorretrofitgroup.com</div>
  </section>

  <section class="card card--back">
    <div class="back__brand">
      <span class="back__brand-name">QUILLMOOR</span>
      <span class="back__brand-mark"></span>
    </div>
    <div class="back__brand-sub">QUILLMOOR RETROFIT GROUP, LLC.</div>

    <div class="person">
      <div class="person__name">DANIEL MARSH</div>
      <div class="person__title">CEO/FOUNDER</div>
    </div>
    <div class="divider"></div>

    <ul class="contacts">
      <li>
        <svg viewBox="0 0 16 16"><path d="M3.5 1l2.6 3-1.5 1.8c.9 2 2.4 3.6 4.4 4.6l1.8-1.5 3 2.6-1.7 2.5C7 13.5 2.4 9 1 3.2z"/></svg>
        555 201 4417
      </li>
      <li>
        <svg viewBox="0 0 16 16"><path d="M4.5 0h7a1 1 0 0 1 1 1v14a1 1 0 0 1-1 1h-7a1 1 0 0 1-1-1V1a1 1 0 0 1 1-1zm1 2v10h5V2zm2.5 11a1 1 0 1 0 0 2 1 1 0 0 0 0-2z"/></svg>
        555 738 2096
      </li>
      <li>
        <svg viewBox="0 0 16 16"><path d="M4 1h8v4H4zM1 6h14v7h-2v-2H3v2H1zm3 6h8v3H4z"/></svg>
        555 904 6183
      </li>
      <li>
        <svg viewBox="0 0 16 16"><path d="M1 3h14v1.2L8 9 1 4.2zm0 2.6l7 4.8 7-4.8V13H1z"/></svg>
        daniel@quillmoordesk.com
      </li>
    </ul>

    <div class="address">
      1420 Tallowbrook Lane<br>
      Ferncastle, Oregon 97024<br>
      www.quillmoordesk.com
    </div>

    <div class="band"></div>
  </section>
</body>
</html>
```